Building / construction Bussiness card design

I need a new design and logo for my company KTR I am a builder who can project manage or design and construct any kind of building, Residential, Commercial and industrial construction.

On the face side of the card I would like to have just the logo.

Industry/Entity Type

Construction

Contact Information for Business Card

KTR Kestrel Timberline Ridge
ABN:48 392 715 604
Oliver Tranmere
Licenced Builders
0472 685 214
oliver@kestreltimberline.com.au
PO Box 527 Wendlow BC 2693

```html
<!DOCTYPE html>
<html lang="en">
<head>
<meta charset="utf-8">
<title>KTR Kestrel Timberline Ridge – Business Card</title>
<link href="https://fonts.googleapis.com/css2?family=Saira:wght@400;500;600&display=swap" rel="stylesheet">
<style>
  :root {
    --backdrop: #1c1e21;
    --card-grey: #5a5b5d;
    --card-grey-light: #8a8b8d;
    --card-grey-dark: #48494b;
    --brand-blue: #0a98da;
    --text-white: #ffffff;
    --text-soft: #e9eaeb;
  }
  * { margin: 0; padding: 0; box-sizing: border-box; }
  html, body {
    width: 1200px; height: 860px; overflow: hidden;
    background: var(--backdrop);
    font-family: "Saira", "Arial", sans-serif;
  }
  .canvas {
    position: relative; width: 1200px; height: 860px;
    display: flex; align-items: center; justify-content: center; gap: 50px;
  }
  .card {
    position: relative; width: 525px; height: 300px; overflow: hidden;
    box-shadow: 0 12px 30px rgba(0,0,0,.45);
  }

  /* Contact side */
  .card-contact {
    background: radial-gradient(circle at 68% 55%, var(--card-grey-light) 0%, var(--card-grey) 45%, var(--card-grey-dark) 100%);
    color: var(--text-white);
    padding: 30px 40px;
  }
  .holder-name {
    font-size: 22px; font-weight: 600; letter-spacing: 1.5px; text-transform: uppercase;
    line-height: 1.3;
  }
  .holder-role {
    font-size: 14px; color: var(--brand-blue); letter-spacing: .5px; line-height: 1.3;
  }
  .postal-address {
    font-size: 14px; line-height: 1.35; margin-top: 14px; color: var(--text-soft);
    font-style: normal;
  }
  .contact-list { list-style: none; margin-top: 12px; }
  .contact-item {
    display: flex; align-items: center; gap: 10px;
    font-size: 13px; line-height: 21px; color: var(--text-soft); letter-spacing: .6px;
  }
  .contact-icon { width: 14px; height: 14px; flex: none; }

  /* Brand side */
  .card-brand { background: var(--brand-blue); }
  .brand-name {
    position: absolute; left: 258px; top: 150px;
    transform: translate(-50%, -50%) rotate(-90deg);
    white-space: nowrap;
    color: var(--text-white); font-size: 19px; font-weight: 500; letter-spacing: 1px;
  }
  .social-strip {
    position: absolute; right: 0; top: 0; width: 150px; height: 100%;
    background: var(--card-grey);
  }
  .social-line {
    position: absolute; bottom: 22px;
    display: flex; align-items: center; gap: 10px;
    transform-origin: left bottom; transform: rotate(-90deg);
    white-space: nowrap;
    color: var(--text-white); font-size: 23px; font-weight: 500; letter-spacing: 1px;
  }
  .social-line.first { left: 62px; }
  .social-line.second { left: 102px; }
  .social-mark { width: 24px; height: 24px; flex: none; border-radius: 3px; }
  .social-mark.muted { background: #6b7fae; }
  .social-mark.bright { background: var(--brand-blue); }
</style>
</head>
<body>
<main class="canvas">

  <section class="card card-contact" aria-label="Contact side">
    <h1 class="holder-name">Oliver Tranmere</h1>
    <p class="holder-role">Licenced Builders</p>
    <address class="postal-address">PO Box 527<br>Wendlow BC 2693<br>ABN: 48 392 715 604</address>
    <ul class="contact-list">
      <li class="contact-item">
        <svg class="contact-icon" viewBox="0 0 16 16" aria-hidden="true"><path d="M4 1l3 3-2 2c1 2 3 4 5 5l2-2 3 3-2 2C7 14 2 9 2 3z" fill="none" stroke="#0a98da" stroke-width="1.5"/></svg>
        <span>0472 685 214</span>
      </li>
      <li class="contact-item">
        <svg class="contact-icon" viewBox="0 0 16 16" aria-hidden="true"><rect x="4" y="1" width="8" height="14" rx="1.5" fill="none" stroke="#0a98da" stroke-width="1.5"/><line x1="7" y1="12.5" x2="9" y2="12.5" stroke="#0a98da" stroke-width="1.5"/></svg>
        <span>0472 685 214</span>
      </li>
      <li class="contact-item">
        <svg class="contact-icon" viewBox="0 0 16 16" aria-hidden="true"><rect x="1" y="6" width="14" height="8" rx="1" fill="#0a98da"/><rect x="4" y="1" width="8" height="5" fill="none" stroke="#0a98da" stroke-width="1.5"/></svg>
        <span>0472 685 214</span>
      </li>
      <li class="contact-item">
        <svg class="contact-icon" viewBox="0 0 16 16" aria-hidden="true"><rect x="1" y="3" width="14" height="10" rx="1" fill="#0a98da"/><path d="M1.5 3.5L8 9l6.5-5.5" fill="none" stroke="#5a5b5d" stroke-width="1.3"/></svg>
        <span>oliver@kestreltimberline.com.au</span>
      </li>
      <li class="contact-item">
        <svg class="contact-icon" viewBox="0 0 16 16" aria-hidden="true"><circle cx="8" cy="8" r="6.5" fill="none" stroke="#0a98da" stroke-width="1.5"/><ellipse cx="8" cy="8" rx="2.8" ry="6.5" fill="none" stroke="#0a98da" stroke-width="1.2"/><line x1="1.5" y1="8" x2="14.5" y2="8" stroke="#0a98da" stroke-width="1.2"/></svg>
        <span>www.kestreltimberline.com.au</span>
      </li>
    </ul>
  </section>

  <section class="card card-brand" aria-label="Brand side">
    <p class="brand-name">KTR Kestrel Timberline Ridge</p>
    <div class="social-strip">
      <p class="social-line first"><span class="social-mark muted"></span>follow/kestrelridge</p>
      <p class="social-line second"><span class="social-mark bright"></span>news/kestrelridge</p>
    </div>
  </section>

</main>
</body>
</html>
```